Velmarsh Group Webpage Design

We need a new website for our company. The company is Velmarsh Group Pty Ltd. We are in the business of Asbestos Removal; Demolition; Earthworks and Transport. We do not advertise and would like our website to be a reference point for our clients / potential clients and also to make our services known to those searching the internet for the services we offer. Some examples of the style of website we are after are:
http://www.quarnedemolition-example.com.au/
http://m.brintowerdemolitions-example.com.au/
http://www.fenwarddemolition-example.com.au
http://www.tolvik-example.com.au
http://www.ptrservices-example.com.au
http://www.steadfast-dismantling-example.com.au
We will need to work on content. Enclosed is an example. We also need to purchase the domain velmarshgroup-example.com.au and need to set up email accounts and ensure the website is mobile friendly. We have a company logo and have built our business on delivering professional, quality services on time. We would like the webpage to be simple, informative and professional - black and white / grey themed. We would also like to add a photo gallery etc later.

Industry/Entity Type

Construction

Coding

Coded - Design and coding required

Number of Pages Required

1 page

Colors
000000
fcfcfc
959595
dddddd

Requirements
Must have
• Information regarding the services we provide

```html
<!DOCTYPE html>
<html lang="en">
<head>
<meta charset="utf-8">
<title>Velmarsh Group</title>
<link href="https://fonts.googleapis.com/css2?family=Michroma&family=Open+Sans:wght@400;600;700&display=swap" rel="stylesheet">
<style>
:root{
  --accent:#b65a51;
  --ink:#222222;
  --body:#555555;
  --grey:#959595;
  --light:#dddddd;
  --paper:#fcfcfc;
  --dark:#333333;
  --black:#000000;
}
*{box-sizing:border-box;margin:0;padding:0}
html,body{width:1200px;height:3291px;overflow:hidden;background:var(--paper)}
body{font-family:"Open Sans",Arial,sans-serif;color:var(--body);position:relative}
.display{font-family:"Michroma","Arial Black",sans-serif}
section,footer{position:absolute;left:0;width:1200px;overflow:hidden}
.abs{position:absolute}

/* hero */
.hero{top:0;height:658px}
.hero-photo{position:absolute;inset:0;background:linear-gradient(180deg,#eef0f2 0%,#d9dde0 45%,#b9b3aa 70%,#8e877c 100%)}
.main-nav{position:absolute;top:18px;left:0;width:1200px;display:flex;justify-content:center;gap:46px}
.main-nav a{font-family:"Michroma",sans-serif;font-size:15px;color:var(--black);text-decoration:none;letter-spacing:1px}
.main-nav a.active{color:var(--accent)}
.brand{position:absolute;top:112px;width:1200px;text-align:center}
.brand-name{font-size:68px;color:var(--accent);letter-spacing:10px;line-height:1}
.brand-sub{margin-top:16px;display:flex;justify-content:center;align-items:center;gap:22px;font-family:"Michroma",sans-serif;font-size:17px;letter-spacing:12px;color:var(--ink)}
.rule{display:inline-block;height:2px;width:150px;background:var(--ink)}

/* welcome */
.welcome{top:658px;height:553px;background:var(--paper)}
.welcome h1{position:absolute;top:48px;width:1200px;text-align:center;font-size:46px;font-weight:400;color:var(--ink);letter-spacing:3px}
.welcome h1 span{color:var(--accent)}
.sub-line{position:absolute;width:1200px;display:flex;justify-content:center;align-items:center;gap:18px;font-family:"Michroma",sans-serif;color:var(--ink)}
.sub-line .rule{background:var(--accent);width:160px;height:2px}
.welcome .sub-line{top:106px;font-size:19px;letter-spacing:3px}
.intro{position:absolute;top:150px;left:210px;width:780px;text-align:center;font-size:12.5px;line-height:22px;color:var(--body)}
.card{position:absolute;top:301px;width:334px;height:187px;display:flex;flex-direction:column;align-items:center;justify-content:center;color:#fff}
.card-photo{position:absolute;inset:0}
.card h3{position:relative;font-family:"Michroma",sans-serif;font-weight:400;font-size:22px;letter-spacing:2px}
.card p{position:relative;font-size:14px;margin-top:6px}
.card .btn{position:relative;margin-top:10px;background:var(--accent);padding:6px 12px;font-size:14px;border-radius:2px}

/* services */
.services{top:1211px;height:623px;color:#fff}
.services-photo{position:absolute;inset:0;background:linear-gradient(120deg,#2a2a2c 0%,#3d3b35 30%,#5a4f34 55%,#2e2e30 100%)}
.services h2{position:absolute;top:55px;width:1200px;text-align:center;font-size:44px;font-weight:400;color:var(--accent);letter-spacing:3px}
.services .sub-line{top:112px;font-size:22px;letter-spacing:4px;color:#fff}
.services .sub-line .rule{background:#fff;width:80px;height:1px}
.services-intro{position:absolute;top:163px;left:190px;width:820px;text-align:center;font-size:13.5px;line-height:23px}
.service{position:absolute;width:300px;font-size:13.5px;line-height:22px}
.service h4{font-family:"Michroma",sans-serif;font-weight:400;font-size:17px;letter-spacing:1px;margin-bottom:6px}
.service.left{text-align:right}
.service h4.red{color:var(--accent)}
.s-icon{position:absolute;width:92px;height:92px}
.globe{position:absolute;left:475px;top:290px;width:250px;height:250px;border-radius:50%;background:radial-gradient(circle at 40% 45%,#5a8fb0 0%,#4f7a4a 45%,#2f5a2c 75%,#1f2d1c 100%)}

/* safety & environment */
.values{top:1834px;height:617px;background:var(--paper)}
.value-photo{position:absolute;top:56px;width:480px;height:230px}
.value-text{position:absolute;top:313px;width:480px;font-size:15px;line-height:24px;color:#333}
.value-text ul{margin-top:14px;list-style:none}
.value-text li{font-size:12.5px;line-height:24px;color:var(--body)}
.value-text li::before{content:"•";margin-right:10px}

/* contact */
.contact{top:2451px;height:500px}
.contact-photo{position:absolute;inset:0;background:linear-gradient(180deg,#1c1a1c 0%,#3a2f28 45%,#4a3a2c 70%,#1d1b1d 100%)}
.contact h2{position:absolute;top:50px;width:1200px;text-align:center;font-size:42px;font-weight:400;color:#fff;letter-spacing:4px}
.contact .sub-line{top:106px;font-size:22px;color:#fff}
.contact .sub-line .rule{width:230px;height:2px;background:var(--accent)}
.field{position:absolute;left:77px;width:511px;height:42px;border:1px solid rgba(255,255,255,.75);color:#fff;font-size:13px;padding:11px 10px}
.field.message{left:612px;width:511px;height:199px}
.send{position:absolute;left:522px;top:384px;width:154px;height:48px;background:var(--light);border-radius:3px;font-family:"Michroma",sans-serif;font-size:20px;color:#333;text-align:center;line-height:48px;letter-spacing:2px}

/* copyright */
.copyright{top:2951px;height:88px;background:#fff;text-align:center;font-family:"Michroma",sans-serif;font-size:14px;color:var(--ink);line-height:78px;letter-spacing:1px}
.copyright span{color:var(--accent)}

/* footer */
.site-footer{top:3039px;height:252px;background:var(--dark);color:#fff;overflow:visible}
.to-top{position:absolute;left:574px;top:-24px;width:52px;height:50px;background:var(--dark)}
.contact-card{position:absolute;top:30px;width:330px}
.contact-card h5{font-family:"Michroma",sans-serif;font-weight:400;font-size:17px;letter-spacing:2px}
.contact-card .role{font-weight:700;font-size:15px;margin-top:8px}
.contact-card .line{font-size:12.5px;margin-top:10px;display:flex;align-items:center;gap:14px;color:#ddd}
.contact-card.right{text-align:right}
.contact-card.right .line{justify-content:flex-end}
.find-us{position:absolute;top:50px;width:1200px;text-align:center;font-family:"Michroma",sans-serif;font-size:16px;letter-spacing:2px}
.social{position:absolute;top:87px;left:526px;display:flex;gap:13px}
.social span{width:40px;height:40px;border:1px solid #888;display:block}
.social span.on{border-color:var(--accent)}
.sitemap{position:absolute;top:160px;width:1200px;text-align:center;font-family:"Michroma",sans-serif;font-size:15px;letter-spacing:2px}
.foot-nav{position:absolute;top:207px;width:1200px;display:flex;justify-content:center;gap:0}
.foot-nav a{font-family:"Michroma",sans-serif;font-size:12px;color:#999;text-decoration:none;padding:0 24px;border-left:1px solid #555;line-height:16px;position:relative}
.foot-nav a:first-child{border-left:none}
.foot-nav a.active{color:var(--accent)}
.foot-nav a.active::after{content:"";position:absolute;left:2px;right:2px;bottom:-12px;height:2px;background:var(--accent)}
</style>
</head>
<body>

<section class="hero">
  <div class="hero-photo" role="img" aria-label="Wheel loader and excavator working on a rubble site in front of a city skyline"></div>
  <nav class="main-nav">
    <a class="active" href="#">HOME</a><a href="#">ABOUT US</a><a href="#">SERVICES</a><a href="#">SAFETY</a><a href="#">ENVIRONMENT</a><a href="#">CONTACT US</a>
  </nav>
  <div class="brand">
    <div class="brand-name display">VELMARSH</div>
    <div class="brand-sub"><span class="rule"></span>GROUP<span class="rule"></span></div>
  </div>
</section>

<section class="welcome">
  <h1 class="display">WELCOME TO THE <span>VELMARSH</span></h1>
  <div class="sub-line"><span class="rule"></span>GROUP<span class="rule"></span></div>
  <p class="intro">Velmarsh Transport Pty Ltd was established by Director Adrian Velmarsh in 2002 with a focus providing services within the transport industry. Over time the company has developed and expanded to include the provision of Earthworks and Demolition. Adrian has over 10 years' experience working at all levels within these industries focusing primarily on Demolition and Earthworks in recent times. Velmarsh Transport and Demolition is built on core values of Service, Safety and Environment and are dedicated to delivering a quality, safe, cost effective, efficient and reliable service.</p>

  <div class="card" style="left:77px">
    <div class="card-photo" role="img" aria-label="Transport truck on a work site" style="background:linear-gradient(135deg,#4a4642,#6b5a48 55%,#3a3734)"></div>
    <h3>TRANSPORT</h3><p>100 Projects</p><span class="btn">Browse Photo</span>
  </div>
  <div class="card" style="left:433px">
    <div class="card-photo" role="img" aria-label="Excavator demolishing a building" style="background:linear-gradient(135deg,#5a4f40,#7a6a52 50%,#3e3830)"></div>
    <h3>DEMOLITION</h3><p>200 Projects</p>
  </div>
  <div class="card" style="left:790px">
    <div class="card-photo" role="img" aria-label="Earthmoving machinery at a quarry" style="background:linear-gradient(135deg,#2e2e2c,#56503c 55%,#232321)"></div>
    <h3>EARTHMOVING</h3><p>200 Projects</p>
  </div>
</section>

<section class="services">
  <div class="services-photo" role="img" aria-label="Large mining haul trucks and excavator, darkened"></div>
  <h2 class="display">SERVICES</h2>
  <div class="sub-line"><span class="rule"></span>WE PROVIDE<span class="rule"></span></div>
  <p class="services-intro">Velmarsh Transport and Demolition offer an extensive range of services including Demolition, Earthworks and Asbestos Removal. We make it our business to consult with clients, assess their needs and tailor a complete solution. We pride ourselves on a professional approach and timely delivery of services.</p>

  <div class="globe" role="img" aria-label="Globe illustration with city and green landscape"></div>

  <div class="service left" style="left:45px;top:312px"><h4>DEMOLITION</h4>Velmarsh Transport and Demolition provide an extensive range of demolition services.</div>
  <svg class="s-icon" style="left:356px;top:297px" viewBox="0 0 92 92"><circle cx="46" cy="46" r="44" fill="#fff"/><circle cx="46" cy="46" r="38" fill="var(--accent)"/><circle cx="46" cy="46" r="20" fill="none" stroke="#fff" stroke-width="4"/><path d="M30 50h32" stroke="#fff" stroke-width="4"/></svg>

  <div class="service left" style="left:45px;top:455px"><h4 class="red">EARTHWORKS</h4>Velmarsh Transport and Demolition possess all necessary equipment and skilled personnel to provide earthmoving services as it is</div>
  <svg class="s-icon" style="left:370px;top:440px" viewBox="0 0 92 92"><circle cx="46" cy="46" r="44" fill="var(--accent)"/><rect x="26" y="44" width="34" height="14" fill="#fff"/><path d="M60 50l10-14" stroke="#fff" stroke-width="4"/><circle cx="32" cy="62" r="5" fill="#fff"/><circle cx="54" cy="62" r="5" fill="#fff"/></svg>

  <svg class="s-icon" style="left:735px;top:297px" viewBox="0 0 92 92"><circle cx="46" cy="46" r="44" fill="var(--accent)"/><circle cx="46" cy="42" r="16" fill="none" stroke="#fff" stroke-width="4"/><rect x="36" y="58" width="20" height="10" fill="#fff"/></svg>
  <div class="service" style="left:842px;top:312px"><h4 class="red">ASBESTOS</h4>Asbestos is a naturally occurring silicate mineral made up of tiny fibres.</div>

  <svg class="s-icon" style="left:735px;top:440px" viewBox="0 0 92 92"><circle cx="46" cy="46" r="44" fill="var(--accent)"/><circle cx="46" cy="46" r="28" fill="none" stroke="#fff" stroke-width="4"/><text x="46" y="54" text-anchor="middle" font-family="Open Sans, sans-serif" font-weight="700" font-size="22" fill="#fff">24</text></svg>
  <div class="service" style="left:842px;top:455px"><h4 class="red">HOURS OF OPERATION</h4>Velmarsh Transport and Demolition operate Monday to Saturday.</div>
</section>

<section class="values">
  <div class="value-photo" style="left:77px;background:linear-gradient(180deg,#f2a73a 0%,#e07a22 45%,#c9c9c9 60%,#eeeeee 100%)" role="img" aria-label="Orange 3D safety lettering with hard hat over rubble"></div>
  <div class="value-photo" style="left:643px;background:linear-gradient(180deg,#fbfbfb 0%,#f0dada 22%,#7da9d6 40%,#8fb46a 70%,#4f8a2c 100%)" role="img" aria-label="Environment lettering above green hill with city towers"></div>
  <div class="value-text" style="left:77px">
    <p>The safety of our clients, workforce and wider community is of paramount importance to Velmarsh Transport and Demolition. We employ a comprehensive Safety Management System ensuring:</p>
    <ul><li>A safe work environment</li><li>Safe plant and structures</li><li>Safe systems of work</li><li>Safe use, handling and storage – plant, structures, substances</li><li>Adequate resources</li><li>Information, training, instruction and supervision</li><li>Continued monitoring</li></ul>
  </div>
  <div class="value-text" style="left:643px">
    <p>Velmarsh Transport &amp; Demolition is committed to reducing the environmental impact of its undertakings. Environmental considerations and deeply embedded within business culture to ensure the environment is preserved for future generations. We employ an Environmental Management System which includes / considers:</p>
    <ul><li>Environmental Management Plans</li><li>Vegetation / Tree Protection</li><li>Reuse / salvage</li><li>Recycling</li></ul>
  </div>
</section>

<section class="contact">
  <div class="contact-photo" role="img" aria-label="City skyline at night with lit towers"></div>
  <h2 class="display">GET IN TOUCH WITH</h2>
  <div class="sub-line"><span class="rule"></span>US<span class="rule"></span></div>
  <div class="field" style="top:156px">Your Name:</div>
  <div class="field" style="top:209px">Your E-mail Address:</div>
  <div class="field" style="top:262px">Your Phone No.:</div>
  <div class="field" style="top:315px">Subject:</div>
  <div class="field message" style="top:156px">Your Message Here:</div>
  <div class="send">SEND</div>
</section>

<section class="copyright">© <span>VELMARSH GROUP</span> 2015. ALL RIGHTS RESERVED.</section>

<footer class="site-footer">
  <svg class="to-top" viewBox="0 0 52 50"><rect width="52" height="50" fill="#333"/><path d="M15 32l11-13 11 13z" fill="var(--accent)"/></svg>

  <div class="contact-card" style="left:80px">
    <h5>ADRIAN VELMARSH</h5>
    <div class="role">Director</div>
    <div class="line"><svg width="14" height="14" viewBox="0 0 14 14"><path d="M7 1a4 4 0 0 1 4 4c0 3-4 8-4 8S3 8 3 5a4 4 0 0 1 4-4z" fill="#999"/></svg>PO Box 000 HARLOW QLD 4000</div>
    <div class="line"><svg width="14" height="12" viewBox="0 0 14 12"><rect x="1" y="1" width="12" height="10" fill="none" stroke="#999" stroke-width="1.5"/><path d="M1 1l6 5 6-5" fill="none" stroke="#999" stroke-width="1.5"/></svg>vtdemolition@example-mail.com</div>
    <div class="line"><svg width="14" height="14" viewBox="0 0 14 14"><path d="M3 1l3 3-2 2c1 2 2 3 4 4l2-2 3 3-2 2C6 13 1 8 1 3z" fill="#999"/></svg>0400 000 123</div>
  </div>

  <div class="find-us">FIND US</div>
  <div class="social"><span class="on"></span><span></span><span></span></div>
  <div class="sitemap">SITE MAP</div>

  <div class="contact-card right" style="left:790px">
    <h5>NADIA KORELL</h5>
    <div class="role">Administration</div>
    <div class="line">PO Box 000 HARLOW QLD 4000<svg width="14" height="14" viewBox="0 0 14 14"><path d="M7 1a4 4 0 0 1 4 4c0 3-4 8-4 8S3 8 3 5a4 4 0 0 1 4-4z" fill="#999"/></svg></div>
    <div class="line">vtdemolition@example-mail.com<svg width="14" height="12" viewBox="0 0 14 12"><rect x="1" y="1" width="12" height="10" fill="none" stroke="#999" stroke-width="1.5"/><path d="M1 1l6 5 6-5" fill="none" stroke="#999" stroke-width="1.5"/></svg></div>
    <div class="line">0400 000 456<svg width="14" height="14" viewBox="0 0 14 14"><path d="M3 1l3 3-2 2c1 2 2 3 4 4l2-2 3 3-2 2C6 13 1 8 1 3z" fill="#999"/></svg></div>
  </div>

  <nav class="foot-nav">
    <a class="active" href="#">HOME</a><a href="#">ABOUT US</a><a href="#">SERVICES</a><a href="#">SAFETY</a><a href="#">ENVIRONMENT</a><a href="#">CONTACT US</a>
  </nav>
</footer>

</body>
</html>
```